Professional Services - letterhead / business cards

The company (velmora partners) will provide services to Investment Funds and large investors in Spain. I have recently chosen a logo that I am attaching.

I would like a simple stationary design that i could use as letter head, business cards and "with compliments" cards.

I am not quite sure which color I will mostly use for the logo, in the email signature I will probably lean towards the white background and grey letters. I am attaching my favourite options.

Target Market(s)

Large Multinationals, Investment funds and Law firms

Industry/Entity Type

Business

Requirements
Must have
• my details are:
Luis R. Abadal
Velmora Partners S.L.
Casa de Torrelumbre
Calle de Vientoalto 27
28014 Madrid
T: +34 (91) 387-2265
M: +34 (646) 819-054
e-mail: labadal@velmorapartners.com

```html
<!DOCTYPE html>
<html lang="en">
<head>
<meta charset="utf-8">
<title>Velmora Partners — Stationery</title>
<link href="https://fonts.googleapis.com/css2?family=Mulish:wght@400;600&family=Open+Sans:wght@400&family=Great+Vibes&display=swap" rel="stylesheet">
<style>
  :root {
    --navy: #2b2870;
    --paper: #ffffff;
    --paper-edge: #d9d9d9;
    --sheet-shade: #f1f1f1;
    --ink-soft: #6b6b7a;
    --ghost: #e2e1ec;
    --stage: #ecebe8;
    --label: #55535a;
  }
  * { box-sizing: border-box; margin: 0; padding: 0; }
  html, body { width: 1200px; height: 368px; overflow: hidden; }
  body {
    position: relative;
    background: var(--stage);
    font-family: "Mulish", "Helvetica Neue", Arial, sans-serif;
    color: var(--navy);
  }
  .piece {
    position: absolute;
    background: var(--paper);
    border: 1px solid var(--paper-edge);
    box-shadow: 0 1px 4px rgba(0,0,0,.12);
    overflow: hidden;
  }
  .letterhead { top: 4px; width: 259px; height: 332px;
    background: linear-gradient(160deg, #fff 40%, var(--sheet-shade)); }
  .letterhead--option-1 { left: 0; }
  .letterhead--option-2 { left: 285px; }
  .wordmark {
    position: absolute;
    font-family: "Mulish", "Helvetica Neue", Arial, sans-serif;
    font-weight: 400;
    color: var(--navy);
    white-space: nowrap;
    letter-spacing: .01em;
  }
  .letterhead .wordmark { top: 14px; font-size: 15px; }
  .letterhead--option-1 .wordmark { left: 66px; }
  .letterhead--option-2 .wordmark { left: 12px; }
  .ghost-name {
    position: absolute; left: 18px; top: 150px;
    font-size: 62px; font-weight: 400; color: var(--ghost);
    transform: rotate(-45deg); transform-origin: left top;
    top: 250px; white-space: nowrap;
  }
  .letter-footer {
    position: absolute; bottom: 7px; left: 0; right: 0;
    text-align: center; font-size: 4.6px; color: var(--ink-soft);
  }
  .letter-contact {
    position: absolute; top: 9px; right: 10px;
    font-size: 4.6px; line-height: 1.35; color: var(--ink-soft);
  }
  .option-label {
    position: absolute; top: 344px;
    font-family: "Open Sans", Arial, sans-serif; font-size: 19px; color: var(--label);
  }
  .option-label--1 { left: 86px; }
  .option-label--2 { left: 370px; }
  .option-label--compliments { left: 1020px; top: 242px; font-size: 14px; }

  .envelope { width: 289px; height: 129px; }
  .envelope--back { left: 632px; top: 4px; }
  .envelope--open { left: 568px; top: 60px; }
  .envelope--front { left: 599px; top: 117px;
    background: linear-gradient(180deg, #fff, #ececec); }
  .envelope svg.flap { position: absolute; left: 0; top: 0; }
  .envelope--back .wordmark { left: 0; right: 0; text-align: center; top: 18px; font-size: 15px; color: #fff; }
  .envelope--open .wordmark { left: 0; right: 0; text-align: center; top: 26px; font-size: 16px; }
  .envelope--front .wordmark { left: 8px; top: 12px; font-size: 12.5px; }
  .envelope--front .return-address {
    position: absolute; left: 8px; top: 34px; font-size: 4.4px; color: var(--ink-soft);
  }

  .business-card { top: 267px; width: 131px; height: 73px; }
  .business-card--details { left: 573px; }
  .business-card--white { left: 708px; }
  .business-card--navy { left: 844px; background: var(--navy); border-color: var(--navy); }
  .business-card--details .wordmark { left: 6px; top: 12px; font-size: 10px; }
  .business-card--white .wordmark,
  .business-card--navy .wordmark { left: 0; right: 0; text-align: center; top: 30px; font-size: 11px; }
  .business-card--navy .wordmark { color: #fff; }
  .card-contact {
    position: absolute; left: 6px; top: 37px;
    font-size: 3.6px; line-height: 1.5; color: var(--ink-soft);
  }
  .card-contact .gap { height: 3px; }
  .card-holder {
    position: absolute; right: 4px; top: 44px; text-align: right;
  }
  .card-holder__name { font-size: 5.6px; font-weight: 600; color: var(--navy); }
  .card-holder__company { font-size: 3.4px; color: var(--ink-soft); }

  .compliments-slip { left: 944px; top: 118px; width: 252px; height: 119px; }
  .compliments-slip .wordmark { left: 12px; top: 16px; font-size: 17px; }
  .slip-contact {
    position: absolute; left: 12px; top: 62px;
    font-size: 5.2px; line-height: 1.55; color: var(--ink-soft);
  }
  .slip-contact .gap { height: 6px; }
  .with-compliments {
    position: absolute; right: 8px; top: 88px;
    font-family: "Great Vibes", cursive; font-size: 16px; color: var(--navy);
  }
  .icon { width: 4px; height: 4px; vertical-align: -0.5px; margin-right: 2px; }
</style>
</head>
<body>

  <!-- Letterhead, option 1 -->
  <section class="piece letterhead letterhead--option-1">
    <div class="wordmark">velmora partners</div>
    <div class="ghost-name" aria-hidden="true">velmora</div>
    <div class="letter-footer">Casa de Torrelumbre, Calle de Vientoalto 27, 28014 Madrid &nbsp;|&nbsp; +34 (91) 387-2265</div>
  </section>
  <div class="option-label option-label--1">Option-1</div>

  <!-- Letterhead, option 2 -->
  <section class="piece letterhead letterhead--option-2">
    <div class="wordmark">velmora partners</div>
    <div class="letter-contact">
      <div>+34 (91) 387-2265</div>
      <div>Casa de Torrelumbre</div>
      <div>Calle de Vientoalto 27</div>
      <div>28014 Madrid</div>
    </div>
  </section>
  <div class="option-label option-label--2">Option-2</div>

  <!-- Envelopes -->
  <section class="piece envelope envelope--back">
    <svg class="flap" width="289" height="129" viewBox="0 0 289 129" aria-hidden="true">
      <path d="M0 0 H289 V4 C250 40 220 52 180 53 H109 C69 52 39 40 0 4 Z" fill="var(--navy)"/>
    </svg>
    <div class="wordmark">velmora</div>
  </section>

  <section class="piece envelope envelope--open">
    <svg class="flap" width="289" height="129" viewBox="0 0 289 129" aria-hidden="true">
      <path d="M0 2 C10 20 30 28 60 36 L144 52 L229 36 C259 28 279 20 289 2" fill="none" stroke="#555" stroke-width=".8"/>
    </svg>
    <div class="wordmark">velmora</div>
  </section>

  <section class="piece envelope envelope--front">
    <div class="wordmark">velmora partners</div>
    <div class="return-address">Casa de Torrelumbre, Calle de Vientoalto 27, 28014 Madrid</div>
  </section>

  <!-- Compliments slip -->
  <section class="piece compliments-slip">
    <div class="wordmark">velmora partners</div>
    <div class="slip-contact">
      <div><svg class="icon" viewBox="0 0 10 10"><circle cx="5" cy="5" r="4" fill="none" stroke="currentColor" stroke-width="1.4"/></svg>+34 (91) 387-2265</div>
      <div><svg class="icon" viewBox="0 0 10 10"><rect x="3" y="1" width="4" height="8" rx="1" fill="currentColor"/></svg>+34 (646) 819-054</div>
      <div><svg class="icon" viewBox="0 0 10 10"><rect x="1" y="2.5" width="8" height="5" fill="none" stroke="currentColor" stroke-width="1.2"/></svg>labadal@velmorapartners.com</div>
      <div class="gap"></div>
      <div>Casa de Torrelumbre</div>
      <div>Calle de Vientoalto 27, 28014 Madrid</div>
    </div>
    <div class="with-compliments">With Compliments</div>
  </section>
  <div class="option-label option-label--compliments">Compliments</div>

  <!-- Business cards -->
  <section class="piece business-card business-card--details">
    <div class="wordmark">velmora partners</div>
    <div class="card-contact">
      <div>+34 (91) 387-2265</div>
      <div>+34 (646) 819-054</div>
      <div>labadal@velmorapartners.com</div>
      <div class="gap"></div>
      <div>Casa de Torrelumbre</div>
      <div>Calle de Vientoalto 27, 28014 Madrid</div>
    </div>
    <div class="card-holder">
      <div class="card-holder__name">Luis R. Abadal</div>
      <div class="card-holder__company">Velmora Partners S.L.</div>
    </div>
  </section>

  <section class="piece business-card business-card--white">
    <div class="wordmark">velmora partners</div>
  </section>

  <section class="piece business-card business-card--navy">
    <div class="wordmark">velmora partners</div>
  </section>

</body>
</html>
```